GlassHaven Artbook for Okanagan Region, British Columbia

Creating an art book: GlassHaven, for the Okanagan Wine Region in British Columbia, Canada. Would like smart, modern, clean and linear...cool, sexy urban, not ugly boring suburban... I need a cover that appeals to the wino in all of us! Title: GlassHaven -Marla Dovicki
Updates
Thank you all kindly for your efforts. I have added some files so that you can get a sense of my aesthetic...it's never easy trying to figure it out, is it? I will hopefully have dimensions of book soon...cheers, Marla
would anyone please design a giant wine bottle with the wine label that looks like a label but says glasshaven...just curious to see if it works as a design or not...thank you.
Target Market(s)
Designing this wine art book of quotes to wineries in Okanagan BC. Buyer is wine lover and tourist ready to spend his vacation bucks on this wonderful book!
Look and feel

```html
<!DOCTYPE html>
<html lang="en">
<head>
<meta charset="utf-8">
<title>GlassHaven — Marla Dovicki</title>
<link rel="stylesheet" href="https://fonts.googleapis.com/css2?family=Questrial&display=swap">
<style>
  :root {
    --paper: #ffffff;
    --band-pink: #ff4785;
    --band-rose: #ff1f4a;
    --band-red: #ff0a0a;
    --band-red-soft: #f80a0a;
    --band-crimson: #c80000;
    --title-pink: #ff4785;
    --title-white: #ffffff;
    --author-red: #ff0a0a;
    --glass-dark: #111111;
    --wine-red: #e00000;
  }
  html, body {
    margin: 0;
    padding: 0;
    width: 1200px;
    height: 1136px;
    overflow: hidden;
    background: var(--paper);
  }
  .cover {
    display: block;
    width: 1200px;
    height: 1136px;
  }
  .cover-text {
    font-family: "Questrial", "Century Gothic", sans-serif;
  }
  .author { fill: var(--author-red); font-size: 38px; }
  .title-first { fill: var(--title-pink); font-size: 253px; }
  .title-second { fill: var(--title-white); font-size: 182px; }
</style>
</head>
<body>
<svg class="cover" viewBox="0 0 1200 1136" xmlns="http://www.w3.org/2000/svg">
  <defs>
    <linearGradient id="glass-tone" x1="0" y1="0" x2="0" y2="1">
      <stop offset="0" stop-color="var(--glass-dark)"/>
      <stop offset="0.22" stop-color="var(--wine-red)"/>
      <stop offset="0.52" stop-color="var(--wine-red)"/>
      <stop offset="0.6" stop-color="var(--glass-dark)"/>
      <stop offset="1" stop-color="var(--glass-dark)"/>
    </linearGradient>
  </defs>

  <g class="background-bands">
    <rect class="band band-paper" x="0" y="0" width="1200" height="430" fill="var(--paper)"/>
    <rect class="band band-pink" x="0" y="430" width="1200" height="53" fill="var(--band-pink)"/>
    <rect class="band band-rose" x="0" y="483" width="1200" height="89" fill="var(--band-rose)"/>
    <rect class="band band-red" x="0" y="572" width="1200" height="124" fill="var(--band-red)"/>
    <rect class="band band-red-soft" x="0" y="696" width="1200" height="194" fill="var(--band-red-soft)"/>
    <rect class="band band-crimson" x="0" y="890" width="1200" height="246" fill="var(--band-crimson)"/>
  </g>

  <rect class="glass-artwork" x="12" y="71" width="442" height="1065" rx="40"
        fill="url(#glass-tone)" role="img"
        aria-label="Black wine glass silhouette holding red wine"/>

  <g class="cover-text">
    <text class="author" x="760" y="95">Marla Dovicki</text>
    <text class="title-first" x="466" y="430">Glass</text>
    <text class="title-second" x="1150" y="566" text-anchor="end">Haven</text>
  </g>
</svg>
</body>
</html>
```